Business Card for Industrial Distributor

We need a business card design for an industrial distributor. We sell machine parts for the manufacturing and oil industry. We would like the cards to look clean and modern but with a touch of industry.

Our colors are blue/white.

Please feel free to visit our website www.korvelpartsco.com

Target Market(s)

mexican manufacturers in the automobile/aerospace industry

Industry/Entity Type

Industrial

Colors
ffffff
0555a3

```html
<!DOCTYPE html>
<html lang="en">
<head>
<meta charset="utf-8">
<title>Korvel Business Card</title>
<link rel="stylesheet" href="https://fonts.googleapis.com/css2?family=Lato:wght@400;700;900&display=swap">
<style>
  :root {
    --brand-blue: #0f58a3;
    --brand-light: #2a72b8;
    --brand-navy: #233a8c;
    --paper: #ffffff;
    --stage: #3c3c3c;
    --muted: #8a8f99;
  }
  * { margin: 0; padding: 0; box-sizing: border-box; }
  html, body { width: 1200px; height: 810px; overflow: hidden; }
  body {
    background: var(--stage);
    font-family: "Lato", sans-serif;
    position: relative;
  }
  .card {
    position: absolute;
    width: 550px;
    height: 314px;
    overflow: hidden;
    box-shadow: 0 8px 24px rgba(0,0,0,0.35);
  }
  .card--front { left: 35px; top: 248px; background: var(--brand-blue); }
  .card--back  { left: 615px; top: 248px; background: var(--paper); }

  .brand {
    position: absolute;
    display: flex;
    align-items: center;
    gap: 12px;
  }
  .brand__dot { border-radius: 50%; flex: none; }
  .brand__name { font-weight: 900; letter-spacing: 1px; line-height: 1; }

  .card--front .brand { left: 120px; top: 120px; }
  .card--front .brand__dot { width: 62px; height: 62px; background: var(--paper); }
  .card--front .brand__name { font-size: 64px; color: var(--paper); }
  .card--front .website {
    position: absolute; left: 0; right: 0; bottom: 34px;
    text-align: center; color: var(--paper); font-size: 13px; letter-spacing: 0.3px;
  }

  .wave { position: absolute; inset: 0; }
  .card--back .brand { left: 34px; top: 36px; }
  .card--back .brand__dot { width: 50px; height: 50px; background: var(--brand-blue); }
  .card--back .brand__name { font-size: 52px; color: var(--brand-navy); }

  .person { position: absolute; right: 34px; top: 30px; text-align: right; }
  .person__name { font-size: 21px; color: var(--brand-navy); line-height: 1.2; }
  .person__title { font-size: 12px; color: var(--muted); margin-top: 2px; }

  .contact {
    position: absolute; left: 60px; bottom: 18px;
    color: var(--paper); font-size: 12.5px; line-height: 1.45;
  }
  .contact__address { margin-bottom: 5px; }
  .contact__row { display: flex; align-items: center; gap: 7px; }
  .contact__row svg { width: 12px; height: 12px; flex: none; }
  .card--back .website {
    position: absolute; right: 34px; bottom: 58px;
    color: var(--paper); font-size: 12.5px;
  }
</style>
</head>
<body>
  <section class="card card--front" aria-label="Card front">
    <div class="brand">
      <span class="brand__dot"></span>
      <span class="brand__name">Korvel</span>
    </div>
    <p class="website">www.korvelpartsco.com</p>
  </section>

  <section class="card card--back" aria-label="Card back">
    <svg class="wave" viewBox="0 0 550 314" preserveAspectRatio="none" aria-hidden="true">
      <path d="M0,150 C100,108 250,118 380,108 C470,100 530,88 550,75 L550,314 L0,314 Z" fill="var(--brand-light)"/>
      <path d="M0,178 C95,135 255,138 390,125 C470,117 530,104 550,93" fill="none" stroke="var(--paper)" stroke-width="4"/>
      <path d="M0,198 C98,152 258,152 395,138 C475,130 530,117 550,106 L550,314 L0,314 Z" fill="var(--brand-blue)"/>
      <path d="M0,190 C96,145 256,146 393,132 C473,124 530,111 550,100" fill="none" stroke="var(--paper)" stroke-width="1.6"/>
    </svg>

    <div class="brand">
      <span class="brand__dot"></span>
      <span class="brand__name">Korvel</span>
    </div>

    <div class="person">
      <p class="person__name">Daniel Reyes</p>
      <p class="person__title">President &amp; CEO</p>
    </div>

    <div class="contact">
      <p class="contact__address">4120 Harbor Line Rd,<br>Laredo, TX 78041</p>
      <p class="contact__row">
        <svg viewBox="0 0 12 12"><path d="M3 1 L5 3.5 L4 5 Q5.5 7.5 7 8 L8.5 7 L11 9 L9.5 11 Q3 10 1 2.5 Z" fill="currentColor"/></svg>
        (956) 555 - 0142
      </p>
      <p class="contact__row">
        <svg viewBox="0 0 12 12"><rect x="3" y="1" width="6" height="4" fill="currentColor"/><rect x="1" y="5" width="10" height="5" rx="1" fill="currentColor"/></svg>
        (956) 555 - 0187
      </p>
      <p class="contact__row">
        <svg viewBox="0 0 12 12"><rect x="1" y="2.5" width="10" height="7" fill="currentColor"/><path d="M1 2.5 L6 6.5 L11 2.5" fill="none" stroke="#0f58a3" stroke-width="1"/></svg>
        sales@korvelpartsco.com
      </p>
    </div>

    <p class="website">www.korvelpartsco.com</p>
  </section>
</body>
</html>
```